"Cedar Hollow Realty" is the name of my real estate company

This is for a: "for sale" sign, looking for a minimalist design, wire frame outline of a midcentury modern homes roof line or elevation?

My name is: Dean Marlowe (needed)
My Cell # is: 415 208 3947 (needed)
My BRE license # is: 02468135 (needed)
BRE needs to be displayed in this format: BRE 02468135 (needed)
The white outline on the sign riders 'pictured" may work on large sign
Note font on pictured rider sign

This design is for a real estate "for sale" sign or sandwich board sign. Do Not include the words "For Sale" on the sign.

The measurements are 36" inches (91.44 cm) Length, or tall X 24" inches (60.90 cm) Wide.

|
3
---- 24 ----
6
|

Sorry I wasn't more specific earlier. I'd like the elements of the sign to be scaled in size according to their importance, from largest to smallest:

My name: Dean Marlowe
My phone number: 415-208-3947
My company name: Cedar Hollow Realty
My license number: BRE 02468135 (This can be much smaller than the smallest text)
Additionally, please incorporate contemporary to mid-century modern elements on the wire frame roofline or a simple roof-like design.

Thank you!

Best regards,
Dean

```html
<!DOCTYPE html>
<html lang="en">
<head>
<meta charset="utf-8">
<title>Dean Marlowe – Yard Sign</title>
<link rel="stylesheet" href="https://fonts.googleapis.com/css2?family=Outfit:wght@400;500&display=swap">
<style>
  :root {
    --backdrop: #e9e9e7;
    --sign-black: #121212;
    --sign-white: #ffffff;
    --ink: #161616;
  }
  * { margin: 0; padding: 0; box-sizing: border-box; }
  html, body {
    width: 1200px;
    height: 1123px;
    overflow: hidden;
    background: var(--backdrop);
  }
  .canvas {
    position: relative;
    width: 1200px;
    height: 1123px;
    font-family: "Outfit", sans-serif;
  }
  .sign {
    position: absolute;
    left: 55px;
    top: 220px;
    width: 1090px;
    height: 728px;
    background: var(--sign-black);
  }
  .brand-band {
    position: absolute;
    left: 20px;
    top: 20px;
    width: 1050px;
    height: 101px;
    background: var(--sign-white);
    display: flex;
    flex-direction: column;
    align-items: center;
    justify-content: center;
    gap: 6px;
  }
  .company {
    color: var(--ink);
    font-size: 46px;
    font-weight: 500;
    letter-spacing: 4px;
    text-transform: uppercase;
    line-height: 1;
  }
  .license {
    color: var(--ink);
    font-size: 22px;
    font-weight: 400;
    letter-spacing: 1px;
    line-height: 1;
  }
  .panel-frame {
    position: absolute;
    left: 20px;
    top: 121px;
    width: 1050px;
    height: 588px;
    border: 2px solid var(--sign-white);
    border-top: none;
  }
  .name-panel {
    position: absolute;
    left: 0;
    top: 0;
    width: 100%;
    height: 387px;
    border-bottom: 2px solid var(--sign-white);
    display: flex;
    flex-direction: column;
    align-items: center;
    justify-content: center;
  }
  .roofline {
    display: block;
    width: 620px;
    height: 40px;
    margin-bottom: 6px;
  }
  .roofline polyline {
    fill: none;
    stroke: var(--sign-white);
    stroke-width: 4;
    stroke-linejoin: miter;
    stroke-linecap: square;
  }
  .agent-name {
    color: var(--sign-white);
    font-size: 156px;
    font-weight: 500;
    line-height: 0.94;
    text-align: center;
    text-transform: uppercase;
    letter-spacing: 2px;
  }
  .phone-panel {
    position: absolute;
    left: 0;
    top: 387px;
    width: 100%;
    height: 199px;
    display: flex;
    align-items: center;
    justify-content: center;
  }
  .phone {
    color: var(--sign-white);
    font-size: 150px;
    font-weight: 400;
    line-height: 1;
    letter-spacing: -1px;
    word-spacing: -6px;
  }
</style>
</head>
<body>
  <div class="canvas">
    <div class="sign">
      <div class="brand-band">
        <span class="company">Cedar Hollow Realty</span>
        <span class="license">BRE 02468135</span>
      </div>
      <div class="panel-frame">
        <div class="name-panel">
          <svg class="roofline" viewBox="0 0 620 40" aria-hidden="true">
            <polyline points="4,6 310,32 616,6"/>
            <polyline points="150,19 150,38"/>
            <polyline points="470,19 470,38"/>
          </svg>
          <span class="agent-name">Dean</span>
          <span class="agent-name">Marlowe</span>
        </div>
        <div class="phone-panel">
          <span class="phone">415 208 3947</span>
        </div>
      </div>
    </div>
  </div>
</body>
</html>
```